I have a logo and need to design the business card and stationery.
Updates

The uploaded logo image named as GREYMARSH CONSTRUCTION which is to be replaced to GREYMARSH CONTRACTS. Kindly add below details and submit the designs- Company name- Greymarsh Engineering Contracts LLP Name & Post- Kelvan Joshi (Designated Partner) Address- Block No.317, Wing C, Tulvo Trade Court, Manek Pural Road, Ruparel Industrial Estate, Goregaon(E), Mumbai - 400 063 Contact- +91 97415 60382 Email- kelvanjoshi@mailbrook.example Website- www.greymarshcontracts.example Contact for Letterhead- +91-22-28754193

Hi Tovin Rahul, We are liking your Design #28860835. We have suggested some changes which are mentioned in feedback. Kindly revert with it asap to finalize this design.

Colors

Designer to choose colors to be used in the design.

```html
<!DOCTYPE html>
<html lang="en">
<head>
<meta charset="utf-8">
<title>Greymarsh Contracts Letterhead</title>
<link href="https://fonts.googleapis.com/css2?family=Arimo:wght@400;700&family=Mulish:wght@700&display=swap" rel="stylesheet">
<style>
  :root {
    --backdrop: #d4d4d4;
    --paper: #fcfcfc;
    --paper-edge: #f7f7f8;
    --ink: #555555;
    --ink-dark: #333333;
    --ink-soft: #6a6a6a;
    --rule: #555555;
    --panel: #ebebeb;
    --sign-tone: #dcdcdc;
  }
  * { margin: 0; padding: 0; box-sizing: border-box; }
  html, body {
    width: 1200px; height: 1079px; overflow: hidden;
    background: var(--backdrop);
  }
  .letterhead {
    position: absolute; left: 236px; top: 24px;
    width: 728px; height: 1030px;
    background: linear-gradient(90deg, var(--paper), var(--paper-edge));
    font-family: "Arimo", Arial, sans-serif;
    color: var(--ink);
    overflow: hidden;
  }
  .brand-mark {
    position: absolute; left: 118px; top: 46px;
    width: 51px; height: 51px; background: var(--ink-dark);
  }
  .brand-name {
    position: absolute; left: 55px; top: 103px; width: 180px;
    text-align: center; font-weight: 700; font-size: 16px;
    line-height: 18px; letter-spacing: 1px; color: var(--ink-dark);
  }
  .address {
    position: absolute; right: 253px; top: 60px;
    text-align: right; font-size: 10.5px; line-height: 13.3px;
    color: var(--ink-soft);
  }
  .divider {
    position: absolute; left: 487px; top: 62px;
    width: 1.5px; height: 50px; background: var(--rule);
  }
  .contacts {
    position: absolute; left: 503px; top: 63px;
    list-style: none; font-size: 10.5px; color: var(--ink-soft);
  }
  .contacts li { display: flex; align-items: center; height: 16px; }
  .contacts svg { width: 8px; height: 8px; margin-right: 6px; fill: var(--ink-dark); }
  .salutation {
    position: absolute; left: 66px; top: 319px;
    font-family: "Mulish", "Century Gothic", sans-serif;
    font-weight: 700; font-size: 16px; color: var(--ink);
  }
  .body-text p {
    position: absolute; left: 65px; width: 610px;
    font-size: 11.7px; line-height: 15px; color: var(--ink);
    white-space: nowrap;
  }
  .p1 { top: 364px; } .p2 { top: 437px; } .p3 { top: 510px; } .p4 { top: 598px; }
  .closing {
    position: absolute; left: 66px; top: 674px;
    font-family: "Mulish", "Century Gothic", sans-serif;
    font-weight: 700; font-size: 9px; color: var(--ink);
  }
  .signature {
    position: absolute; left: 65px; top: 715px;
    width: 120px; height: 38px;
    background: linear-gradient(90deg, var(--sign-tone), #e9e9e9);
  }
  .corner-panel {
    position: absolute; left: 352px; top: 655px;
    width: 376px; height: 375px; background: var(--panel);
  }
</style>
</head>
<body>
<main class="letterhead">
  <header>
    <div class="brand-mark"></div>
    <div class="brand-name">GREYMARSH<br>CONTRACTS</div>
    <address class="address" style="font-style:normal">
      Block No.317, Wing C<br>
      Tulvo Trade Court, Manek Pural Road<br>
      Ruparel Industrial Estate<br>
      Goregaon(E), Mumbai - 400 063
    </address>
    <div class="divider"></div>
    <ul class="contacts">
      <li><svg viewBox="0 0 10 10"><path d="M2 0.5l2 2-1 1.2c.6 1.3 1.6 2.3 2.9 2.9l1.2-1 2 2-1.3 1.6C4.6 9 1 5.4.4 1.8z"/></svg>+91-22-28754193</li>
      <li><svg viewBox="0 0 10 10"><path d="M0 2h10v6H0z M0 2l5 3.5L10 2" stroke="#fff" stroke-width=".8"/></svg>kelvanjoshi@mailbrook.example</li>
      <li><svg viewBox="0 0 10 10"><circle cx="5" cy="5" r="5"/><path d="M0 5h10M5 0v10" stroke="#fff" stroke-width=".8"/></svg>www.greymarshcontracts.example</li>
    </ul>
  </header>

  <h1 class="salutation">Dear Mr. Smith,</h1>

  <section class="body-text">
    <p class="p1">Lorem ipsum dolor sit amet, consectetuer adipiscing elit, sed diam nonmmy nibh euismod tincidunt ut laor<br>eet dolore magna aliquam erat volutpat. Ut wisi enim ad minim veniam, quis nostrud exerci tationmcorper<br>suscipit lobortis nisl ut aliquip ex ea commodo consequat. Duis autem vel eum iriure dolor in hendrerit in<br>vulputate velit esse molestie consequat, vel illum dolore eu feugiat</p>
    <p class="p2">Rorem ipsum dolor sit amet, consectetuer adipiscing elit, sed diam nonmmy nibh euismod tincidunt ut laor<br>eet dolore magna aliquam erat volutpat. Ut wisi enim ad minim veniam, quis nostrud exerci tationmcorper<br>suscipit lobortis nisl ut aliquip ex ea commodo consequat. Duis autem vel eum iriure dolor in hendrerit in<br>vulputate velit esse molest</p>
    <p class="p3">Dorem ipsum dolor sit amet, consectetuer adipiscing elit, sed diam nonmmy nibh euismod tincidunt ut laor<br>eet dolore magna aliquam erat volutpat. Ut wisi enim ad minim veniam, quis nostrud exerci tationmcorper<br>suscipit lobortis nisl ut aliquip ex ea commodo consequat. Duis autem vel eum iriure dolor in hendrerit in<br>suscipit lobortis nisl ut aliquip ex ea commodo consequat. Duis autem vel eum iriure dolor in hendrerit in<br>vulputate velit esse molestie consequat, vel illum</p>
    <p class="p4">Sorem ipsum dolor sit amet, consectetuer adipiscing elit, sed diam nonmmy nibh euismod tincidunt ut laor<br>eet dolore magna aliquam erat volutpat. Ut wisi enim ad minim veniam, quis nostrud exerci tationmcorper<br>suscipit lobortis nisl ut aliquip ex ea commodo consequat. Duis autem vel eum iriure dolor in</p>
  </section>

  <div class="corner-panel"></div>

  <p class="closing">Sincerely,</p>
  <div class="signature" role="img" aria-label="Handwritten signature"></div>
</main>
</body>
</html>
```